Business Card Design

New business card design

Target Market(s)

Residential & Commercial Property Managers

Industry/Entity Type

Plumbing Services

Contact Information for Business Card

Name - Rowan Keddle, title - Director, Phone Number - 0431 286 517, email - rowan@tbk-plumbing.com.au, Company ABN - 73 215 904 386,

Font styles to use
Sans Serif

Colors
0054AA
0677BA
7BADD7
CADEEF
E8F1F8

```html
<!DOCTYPE html>
<html lang="en">
<head>
<meta charset="utf-8">
<title>TBK Plumbing Services – Business Card</title>
<link rel="stylesheet" href="https://fonts.googleapis.com/css2?family=Poppins:wght@300;400;600&display=swap">
<style>
  :root {
    --stage: #222222;
    --paper: #ffffff;
    --navy: #1c232b;
    --taupe: #6f675b;
    --aqua: #29abe2;
    --ink-light: #ffffff;
  }
  * { margin: 0; padding: 0; box-sizing: border-box; }
  html, body {
    width: 1200px; height: 780px; overflow: hidden;
    background: var(--stage);
    font-family: "Poppins", sans-serif;
  }
  .canvas {
    width: 1200px; height: 780px;
    display: flex; align-items: center; justify-content: center; gap: 40px;
  }
  .card {
    width: 560px; height: 320px; position: relative; overflow: hidden;
  }

  /* Front */
  .card-front { background: var(--paper); }
  .brand {
    position: absolute; left: 40px; top: 38px;
  }
  .brand-name {
    font-size: 72px; font-weight: 300; line-height: 1; letter-spacing: 2px;
    color: var(--navy);
    display: flex; align-items: center; gap: 12px;
  }
  .brand-dot {
    width: 14px; height: 14px; border-radius: 50%; background: var(--aqua);
  }
  .brand-tag {
    margin-top: 8px; font-size: 11px; font-weight: 300;
    letter-spacing: 9px; color: var(--taupe);
  }
  .band {
    position: absolute; left: 0; right: 0; top: 188px; height: 64px; display: flex;
  }
  .band-person {
    width: 290px; background: var(--navy);
    padding: 8px 0 0 34px; color: var(--aqua);
  }
  .person-name { font-size: 26px; line-height: 1.1; white-space: nowrap; }
  .person-name .first { font-weight: 600; }
  .person-name .last { font-weight: 300; }
  .person-role { font-size: 12px; color: var(--ink-light); font-weight: 400; margin-left: 128px; }
  .band-contact {
    flex: 1; background: var(--taupe);
    padding: 7px 0 0 22px; list-style: none;
    color: var(--ink-light); font-size: 11px; font-weight: 300; line-height: 17px;
  }
  .band-contact li { display: flex; align-items: center; gap: 7px; }
  .band-contact svg { width: 12px; height: 12px; flex: none; }
  .abn {
    position: absolute; left: 312px; top: 262px;
    font-size: 13px; color: var(--aqua); font-weight: 400; letter-spacing: 0.5px;
  }

  /* Back */
  .card-back {
    background: var(--taupe);
    display: flex; align-items: center; justify-content: center;
  }
  .card-back .brand { position: static; }
  .card-back .brand-name { color: var(--ink-light); font-size: 96px; }
  .card-back .brand-dot { width: 18px; height: 18px; }
  .card-back .brand-tag { color: var(--ink-light); font-size: 13px; letter-spacing: 12px; margin-top: 10px; }
</style>
</head>
<body>
<main class="canvas">

  <section class="card card-front">
    <div class="brand">
      <div class="brand-name">tbk<span class="brand-dot"></span></div>
      <div class="brand-tag">plumbing services</div>
    </div>

    <div class="band">
      <div class="band-person">
        <div class="person-name"><span class="first">Rowan</span> <span class="last">Keddle</span></div>
        <div class="person-role">Director</div>
      </div>
      <ul class="band-contact">
        <li>
          <svg viewBox="0 0 12 12" aria-hidden="true"><circle cx="6" cy="6" r="6" fill="#29abe2"/><path d="M4 3.2c.3-.2.6-.2.8.1l.5.8c.2.3.1.6-.1.8l-.3.2c.3.7.9 1.3 1.6 1.6l.2-.3c.2-.2.5-.3.8-.1l.8.5c.3.2.3.5.1.8-.6.8-1.6.8-2.6.1-1-.7-1.8-1.7-2-2.6-.2-.6 0-1.2.2-1.9z" fill="#fff"/></svg>
          0431 286 517
        </li>
        <li>
          <svg viewBox="0 0 12 12" aria-hidden="true"><circle cx="6" cy="6" r="6" fill="#29abe2"/><circle cx="6" cy="6" r="3.3" fill="none" stroke="#fff" stroke-width=".8"/><path d="M2.7 6h6.6M6 2.7c-1.4 1.8-1.4 4.8 0 6.6M6 2.7c1.4 1.8 1.4 4.8 0 6.6" fill="none" stroke="#fff" stroke-width=".7"/></svg>
          www.tbk-plumbing.com.au
        </li>
        <li>
          <svg viewBox="0 0 12 12" aria-hidden="true"><circle cx="6" cy="6" r="6" fill="#29abe2"/><rect x="3" y="4" width="6" height="4.2" fill="none" stroke="#fff" stroke-width=".8"/><path d="M3 4l3 2.4L9 4" fill="none" stroke="#fff" stroke-width=".8"/></svg>
          rowan@tbk-plumbing.com.au
        </li>
      </ul>
    </div>

    <div class="abn">ABN - 73 215 904 386</div>
  </section>

  <section class="card card-back">
    <div class="brand">
      <div class="brand-name">tbk<span class="brand-dot"></span></div>
      <div class="brand-tag">plumbing services</div>
    </div>
  </section>

</main>
</body>
</html>
```